New Business Card Design Project

Use the flyer uploaded and website www.brightoakbuilders.com for inspiration.
List Our Services on Backside of business cards
Marcus Delling
Harborline Builders Inc.
Licensed General Contractors
858-471-6093

Contact Information for Business Card

Use the flyer uploaded and website www.brightoakbuilders.com for inspiration. List Our Services on Backside of business cards Marcus Delling Harborline Builders Inc. Licensed General Contractors 858-471-6093

```html
<!DOCTYPE html>
<html lang="en">
<head>
<meta charset="UTF-8">
<title>Harborline Builders – Business Card</title>
<link href="https://fonts.googleapis.com/css2?family=Montserrat:wght@300;400;500;600;700&display=swap" rel="stylesheet">
<style>
  :root {
    --backdrop: #8a7558;
    --card-light: #ffffff;
    --card-dark: #1f1f1f;
    --card-dark-edge: #2a2a2a;
    --ink: #111111;
    --ink-soft: #222222;
    --paper-text: #f2f2f2;
    --art-faint: #ececec;
    --art-faint-edge: #f7f7f7;
    --art-dark: #3a3a3a;
    --art-dark-edge: #262626;
  }
  * { margin: 0; padding: 0; box-sizing: border-box; }
  html, body { width: 900px; height: 1200px; overflow: hidden; }
  body {
    background: var(--backdrop);
    font-family: "Montserrat", sans-serif;
    position: relative;
  }
  .card {
    position: absolute;
    border-radius: 22px;
    overflow: hidden;
    box-shadow: 0 8px 18px rgba(0,0,0,0.35);
  }
  .card--front { left: 80px; top: 131px; width: 742px; height: 440px; background: var(--card-light); color: var(--ink); }
  .card--back { left: 78px; top: 638px; width: 744px; height: 440px; background: linear-gradient(135deg, var(--card-dark-edge), var(--card-dark)); color: var(--paper-text); }

  .brand-name { position: absolute; font-weight: 500; letter-spacing: 0.5px; white-space: nowrap; }
  .card--front .brand-name { left: 32px; top: 58px; font-size: 23px; color: var(--ink); }
  .brand-tagline { position: absolute; font-weight: 500; white-space: nowrap; }
  .card--front .brand-tagline { left: 56px; top: 90px; font-size: 11px; letter-spacing: 2.5px; color: var(--ink); }

  .person-name { position: absolute; left: 35px; top: 211px; font-size: 26px; font-weight: 700; }
  .person-role { position: absolute; left: 35px; top: 243px; font-size: 15px; font-weight: 400; color: var(--ink-soft); }

  .contact-list { position: absolute; left: 35px; top: 284px; list-style: none; }
  .contact-item { display: flex; align-items: center; height: 29.5px; font-size: 16px; font-weight: 400; }
  .contact-item svg { width: 17px; height: 17px; margin-right: 13px; fill: var(--ink); flex: none; }

  .license { position: absolute; left: 35px; top: 393px; font-size: 15px; font-weight: 400; }

  .front-art {
    position: absolute; left: 345px; top: 150px; width: 397px; height: 290px;
    background: linear-gradient(160deg, var(--art-faint-edge), var(--art-faint));
  }

  .back-art {
    position: absolute; left: 0; top: 12px; width: 282px; height: 428px;
    background: linear-gradient(180deg, var(--art-dark), var(--art-dark-edge));
  }
  .card--back .brand-name { right: 50px; top: 60px; font-size: 29px; font-weight: 300; letter-spacing: 1px; color: var(--paper-text); }
  .card--back .brand-tagline { right: 50px; top: 101px; font-size: 13px; font-weight: 300; letter-spacing: 2.5px; color: var(--paper-text); }

  .services-title {
    position: absolute; left: 323px; top: 146px; font-size: 20px; font-weight: 600;
    padding-bottom: 4px; border-bottom: 1px solid var(--paper-text);
  }
  .services-list { position: absolute; left: 328px; top: 186px; list-style: none; }
  .service { position: relative; padding-left: 14px; height: 24px; font-size: 16px; font-weight: 400; white-space: nowrap; }
  .service::before {
    content: ""; position: absolute; left: 0; top: 8px; width: 5px; height: 5px;
    border-radius: 50%; background: var(--paper-text);
  }
</style>
</head>
<body>

<section class="card card--front">
  <div class="brand-name">HARBORLINE BUILDERS</div>
  <div class="brand-tagline">LICENSED GENERAL CONTRACTORS</div>

  <div class="person-name">Marcus Delling</div>
  <div class="person-role">Managing Director</div>

  <ul class="contact-list">
    <li class="contact-item">
      <svg viewBox="0 0 24 24"><path d="M6.6 10.8a15 15 0 0 0 6.6 6.6l2.2-2.2a1 1 0 0 1 1-.25 11.4 11.4 0 0 0 3.6.57 1 1 0 0 1 1 1V20a1 1 0 0 1-1 1A17 17 0 0 1 3 4a1 1 0 0 1 1-1h3.5a1 1 0 0 1 1 1c0 1.25.2 2.45.57 3.57a1 1 0 0 1-.25 1z"/></svg>
      858-471-6093
    </li>
    <li class="contact-item">
      <svg viewBox="0 0 24 24"><path d="M3 5h18v2l-9 6-9-6z"/><path d="M3 9l9 6 9-6v10H3z"/></svg>
      info@brightoakbuilders.com
    </li>
    <li class="contact-item">
      <svg viewBox="0 0 24 24"><circle cx="12" cy="12" r="9.5" fill="none" stroke="#111" stroke-width="2"/><path d="M2.5 12h19M12 2.5c3 3 3 16 0 19M12 2.5c-3 3-3 16 0 19" fill="none" stroke="#111" stroke-width="1.8"/></svg>
      www.brightoakbuilders.com
    </li>
  </ul>

  <div class="license">CSLB Licensed No. #1048261</div>

  <div class="front-art" role="img" aria-label="Faint line drawing of a palm tree beside a house outline"></div>
</section>

<section class="card card--back">
  <div class="back-art" role="img" aria-label="Large grey palm tree with a house outline, fading into the dark card"></div>

  <div class="brand-name">HARBORLINE BUILDERS</div>
  <div class="brand-tagline">LICENSED GENERAL CONTRACTORS</div>

  <h2 class="services-title">Our Services</h2>
  <ul class="services-list">
    <li class="service">Remodel: Kitchen &amp; Bath</li>
    <li class="service">Painting: Interior &amp; Exterior</li>
    <li class="service">Flooring: Carpet, Vinyl, Wood</li>
    <li class="service">Window: Door Replacement</li>
    <li class="service">Plumbing: Repair &amp; Upgrades</li>
    <li class="service">Energy Efficient Upgrades</li>
    <li class="service">Deck &amp; Patio Construction</li>
    <li class="service">Water &amp; Mold Damage</li>
    <li class="service">Garage Renovation</li>
  </ul>
</section>

</body>
</html>
```